Home Remodeling company needs a business card design

we need a business card design for home remodeling company in hamilton county, indiana USA. we offers a wide range of construction services including whole house renovations, Design and Build Basements and Kitchen and Bathroom Remodeling . we would like to see designs for both site of business card that use the same color of the company logo and also including all information below :
1- Karim Feltous CEO / General Contractor
2- all company contacts Telephone numbers ( 1-888-DULOM-47 ) ( 317-555-0193) email address ( info@dulomhome.com) website ( www.dulomhome.com ) and social media logos (Facebook- twitter- google plus )
3- company logo
4- licensed . insured . bonded

```html
<!DOCTYPE html>
<html lang="en">
<head>
<meta charset="utf-8">
<title>Dulom Home Remodeling – Business Card</title>
<link rel="stylesheet" href="https://fonts.googleapis.com/css2?family=Open+Sans:wght@400;600;700&display=swap">
<style>
  :root {
    --canvas-bg: #e6e4e1;
    --card-white: #ffffff;
    --card-black: #1c1c1d;
    --card-black-hi: #2c2c2e;
    --brand-red: #d0313a;
    --brand-grey: #3c3d41;
    --text-dark: #2a2a2c;
    --text-light: #f2f2f2;
  }
  * { box-sizing: border-box; margin: 0; padding: 0; }
  html, body {
    width: 1200px; height: 900px; overflow: hidden;
    background: var(--canvas-bg);
    font-family: "Open Sans", Arial, sans-serif;
  }
  .canvas {
    width: 1200px; height: 900px;
    display: flex; flex-direction: column; align-items: center; justify-content: center;
    gap: 56px;
  }
  .card {
    position: relative;
    width: 600px; height: 343px;
    border-radius: 3px;
    overflow: hidden;
    box-shadow: 0 6px 18px rgba(0,0,0,.18);
  }

  /* ---------- front ---------- */
  .card-front { background: var(--card-white); color: var(--text-dark); }
  .card-front .shapes { position: absolute; inset: 0; width: 100%; height: 100%; }
  .person { position: absolute; left: 54px; top: 22px; }
  .person-name { color: var(--brand-red); font-weight: 700; font-size: 17px; line-height: 1.2; }
  .person-role { font-size: 13px; line-height: 1.3; }
  .contacts { position: absolute; left: 26px; top: 150px; list-style: none; }
  .contacts li {
    display: flex; align-items: center; gap: 8px;
    font-size: 14.5px; line-height: 21px;
  }
  .contacts svg { width: 11px; height: 11px; flex: none; }

  /* company name placeholder: one font, one weight, one colour, plain square */
  .brand {
    position: absolute; display: flex; align-items: center; gap: 12px;
  }
  .brand-square { width: 14px; height: 14px; flex: none; }
  .brand-name {
    font-family: "Open Sans", Arial, sans-serif; font-weight: 700;
    font-size: 26px; line-height: 1.2;
  }
  .card-front .brand { left: 300px; top: 138px; }
  .card-front .brand-square { background: var(--brand-red); }
  .card-front .brand-name { color: var(--brand-grey); }

  .socials { position: absolute; left: 352px; top: 256px; display: flex; gap: 10px; }
  .socials span {
    width: 20px; height: 20px; border-radius: 50%;
    background: var(--text-dark);
  }

  /* ---------- back ---------- */
  .card-back {
    background:
      repeating-linear-gradient(0deg, rgba(255,255,255,.035) 0 1px, transparent 1px 3px),
      linear-gradient(160deg, var(--card-black-hi), var(--card-black) 60%);
    color: var(--text-light);
  }
  .card-back .brand { left: 0; right: 0; top: 92px; justify-content: center; }
  .card-back .brand-square { background: var(--text-light); width: 16px; height: 16px; }
  .card-back .brand-name { color: var(--text-light); font-size: 34px; }
  .divider {
    position: absolute; left: 0; right: 0; top: 196px; height: 1px;
    background: linear-gradient(90deg, transparent, rgba(255,255,255,.18), transparent);
  }
  .tagline {
    position: absolute; left: 0; right: 0; top: 214px; text-align: center;
    font-weight: 600; font-size: 19px; letter-spacing: .5px;
  }
</style>
</head>
<body>
<main class="canvas">

  <section class="card card-front" aria-label="Business card front">
    <svg class="shapes" viewBox="0 0 600 343" aria-hidden="true">
      <polygon points="0,16 40,16 32,28 0,28" fill="var(--brand-red)"/>
      <polygon points="30,30 46,30 46,62 6,62" fill="var(--brand-grey)"/>
      <polygon points="0,258 302,258 288,288 0,288" fill="var(--brand-red)"/>
      <polygon points="300,292 600,292 600,343 280,343" fill="var(--brand-grey)"/>
    </svg>

    <div class="person">
      <p class="person-name">Karim Feltous</p>
      <p class="person-role">CEO / General Contractor</p>
    </div>

    <ul class="contacts">
      <li>
        <svg viewBox="0 0 24 24"><path fill="var(--brand-red)" d="M6.6 10.8a15 15 0 0 0 6.6 6.6l2.2-2.2c.3-.3.7-.4 1-.2 1.1.4 2.3.6 3.6.6.6 0 1 .4 1 1V20c0 .6-.4 1-1 1A17 17 0 0 1 3 4c0-.6.4-1 1-1h3.5c.6 0 1 .4 1 1 0 1.3.2 2.5.6 3.6.1.3 0 .7-.2 1z"/></svg>
        1-888-DULOM-47
      </li>
      <li>
        <svg viewBox="0 0 24 24"><path fill="var(--brand-red)" d="M6.6 10.8a15 15 0 0 0 6.6 6.6l2.2-2.2c.3-.3.7-.4 1-.2 1.1.4 2.3.6 3.6.6.6 0 1 .4 1 1V20c0 .6-.4 1-1 1A17 17 0 0 1 3 4c0-.6.4-1 1-1h3.5c.6 0 1 .4 1 1 0 1.3.2 2.5.6 3.6.1.3 0 .7-.2 1z"/></svg>
        317-555-0193
      </li>
      <li>
        <svg viewBox="0 0 24 24"><rect x="2" y="5" width="20" height="14" fill="var(--brand-red)"/><path d="M2 5l10 8 10-8" fill="none" stroke="#fff" stroke-width="2"/></svg>
        info@dulomhome.com
      </li>
      <li>
        <svg viewBox="0 0 24 24"><path d="M10 14a4 4 0 0 0 5.7 0l4-4a4 4 0 0 0-5.7-5.7l-1.5 1.5M14 10a4 4 0 0 0-5.7 0l-4 4a4 4 0 0 0 5.7 5.7l1.5-1.5" fill="none" stroke="var(--text-dark)" stroke-width="2.4" stroke-linecap="round"/></svg>
        www.dulomhome.com
      </li>
    </ul>

    <div class="brand">
      <span class="brand-square"></span>
      <p class="brand-name">Dulom<br>Home Remodeling</p>
    </div>

    <div class="socials" aria-label="Social media links">
      <span></span><span></span><span></span>
    </div>
  </section>

  <section class="card card-back" aria-label="Business card back">
    <div class="brand">
      <span class="brand-square"></span>
      <p class="brand-name">Dulom Home Remodeling</p>
    </div>
    <div class="divider"></div>
    <p class="tagline">Licensed . Insured . Bonded</p>
  </section>

</main>
</body>
</html>
```